Bluefinch Painting needs a Website

We need a website built for a Painting company I own, we mainly do residential painting, but don't want to be limited to that.

Need to have estimate request form.
Need pic's of past projects

I like the look of the website for http://www.harbor-brushworks.com
& "Westlake Home inspections"

My logo that was designed here on ArtHatch on the front page

I would like one of the houses I downloaded as part of the background
of the front page.

Target Market(s)

Home owners

Industry/Entity Type

Painting

Number of Pages Required

1 page

Font styles to use
Serif

Requirements
Must have
• Estimate request form for home owners to fill out -
• Name:
• Phone Number:
• Address:
• E-mail:
• Painting project description:
• And my info to:
• My phone number: (555) 318-7046
• My web address bluefinchpainting.example
Nice to have
• My logo that was designed here on ArtHatch

```html
<!DOCTYPE html>
<html lang="en">
<head>
<meta charset="utf-8">
<title>Bluefinch Painting</title>
<link href="https://fonts.googleapis.com/css2?family=Tinos:wght@400;700&family=Open+Sans:ital,wght@0,400;0,600;0,700;1,400&display=swap" rel="stylesheet">
<style>
  :root {
    --brand-blue: #0b63af;
    --nav-blue: #1467b6;
    --deep-navy: #1b2a44;
    --accent-green: #7db13b;
    --news-bg: #eeeee2;
    --footer-bg: #4b4b4b;
    --text-dark: #222222;
    --text-muted: #555555;
    --white: #ffffff;
  }
  * { box-sizing: border-box; margin: 0; padding: 0; }
  html, body { width: 1200px; height: 2802px; overflow: hidden; }
  body { position: relative; background: var(--white); font-family: "Open Sans", Arial, sans-serif; color: var(--text-dark); }
  .abs { position: absolute; }

  /* Header */
  .site-header { position: absolute; top: 0; left: 0; width: 1200px; height: 103px; background: var(--white); }
  .brand { position: absolute; left: 159px; top: 20px; display: flex; align-items: center; gap: 14px; }
  .brand-square { width: 50px; height: 50px; background: var(--brand-blue); }
  .brand-name { font-family: "Tinos", serif; font-size: 34px; line-height: 32px; color: var(--deep-navy); letter-spacing: 3px; text-transform: uppercase; }
  .social { position: absolute; display: flex; gap: 5px; }
  .social span { width: 18px; height: 18px; border-radius: 50%; background: #8aa7c8; display: block; }
  .header-social { left: 950px; top: 26px; }
  .phone { position: absolute; left: 870px; top: 54px; display: flex; align-items: center; gap: 8px; font-size: 22px; color: var(--text-dark); }

  /* Navigation */
  .main-nav { position: absolute; top: 103px; left: 0; width: 1200px; height: 53px; background: var(--nav-blue); }
  .nav-item { position: absolute; top: 12px; height: 30px; line-height: 30px; font-family: "Tinos", serif; font-size: 19px; color: var(--white); }
  .nav-item.active { background: #c9d9ea; color: var(--deep-navy); padding: 0 14px; }
  .quote-btn { position: absolute; left: 887px; top: 9px; width: 152px; height: 33px; line-height: 33px; text-align: center; background: #d6e1ee; color: var(--deep-navy); font-size: 14px; font-weight: 600; }

  /* Hero */
  .hero { position: absolute; top: 156px; left: 0; width: 1200px; height: 451px; }
  .hero-photo { width: 100%; height: 100%; background: linear-gradient(100deg, #f3f3f3 0%, #e4e4e4 45%, #f5f5f5 70%, #d9d9d9 100%); }
  .hero-caption { position: absolute; left: 152px; top: 409px; width: 896px; height: 42px; background: rgba(80,80,80,0.75); color: var(--white); font-size: 23px; line-height: 42px; padding-left: 14px; }
  .slider-dots { position: absolute; right: 14px; top: 17px; display: flex; gap: 6px; }
  .slider-dots i { width: 8px; height: 8px; border-radius: 50%; background: #bdbdbd; display: block; }
  .slider-dots i.on { background: var(--white); }

  /* Quality section */
  .quality { position: absolute; top: 607px; left: 0; width: 1200px; height: 346px; background: var(--brand-blue); color: var(--white); }
  .quality h1 { position: absolute; left: 170px; top: 42px; font-family: "Tinos", serif; font-weight: 400; font-size: 38px; line-height: 40px; }
  .quality h2 { position: absolute; left: 170px; top: 82px; font-family: "Tinos", serif; font-weight: 400; font-size: 25px; line-height: 28px; }
  .quality p { position: absolute; left: 170px; top: 116px; width: 420px; font-size: 12px; line-height: 19px; }
  .btn-green { position: absolute; background: var(--accent-green); color: var(--white); font-size: 14px; text-align: center; }
  .quality .btn-green { left: 170px; top: 259px; width: 113px; height: 33px; line-height: 33px; color: var(--deep-navy); }
  .quality-photo { position: absolute; left: 619px; top: 49px; width: 408px; height: 238px; border: 3px solid var(--white); background: linear-gradient(90deg, #e2e2dc 0%, #e0572a 35%, #e96b2d 60%, #cbd42b 85%, #e8e8e0 100%); }

  /* Services */
  .services { position: absolute; top: 953px; left: 0; width: 1200px; height: 343px; }
  .services-photo { position: absolute; left: 170px; top: 49px; width: 425px; height: 240px; background: linear-gradient(135deg, #3a5bb0 0%, #5b78c8 45%, #e8d7b0 75%, #c9a56a 100%); }
  .services h2 { position: absolute; left: 616px; top: 40px; font-family: "Tinos", serif; font-weight: 400; font-size: 38px; line-height: 40px; color: var(--text-dark); }
  .services p { position: absolute; left: 619px; top: 86px; width: 420px; font-size: 12px; line-height: 18px; color: var(--text-muted); }
  .service-list { position: absolute; left: 621px; top: 147px; list-style: none; }
  .service-list li { font-size: 15px; line-height: 24px; color: var(--text-dark); padding-left: 20px; position: relative; }
  .service-list li::before { content: ""; position: absolute; left: 2px; top: 9px; width: 7px; height: 7px; border-radius: 50%; background: #666; }
  .btn-blue { position: absolute; background: var(--brand-blue); color: var(--white); font-size: 14px; text-align: center; }
  .services .btn-blue { left: 621px; top: 254px; width: 112px; height: 35px; line-height: 35px; }

  /* Banner */
  .banner { position: absolute; top: 1296px; left: 0; width: 1200px; height: 346px; background: linear-gradient(90deg, #f4f3f0 0%, #ffffff 35%, #ffffff 55%, #f3cc3a 75%, #f1b81a 100%); }
  .banner-title { position: absolute; left: 170px; top: 50px; font-family: "Tinos", serif; color: #1d1d1d; }
  .banner-title .l1 { display: block; font-size: 62px; line-height: 68px; letter-spacing: 1px; }
  .banner-title .l2 { display: block; font-size: 44px; line-height: 52px; letter-spacing: 2px; }

  /* Projects */
  .projects-title { position: absolute; top: 1692px; left: 0; width: 1200px; text-align: center; font-family: "Tinos", serif; font-weight: 400; font-size: 37px; color: var(--text-dark); }
  .project { position: absolute; width: 420px; height: 234px; }
  .p1 { left: 173px; top: 1747px; background: linear-gradient(120deg, #c9a58b 0%, #c8222e 40%, #8b5b48 70%, #d7c3b0 100%); }
  .p2 { left: 607px; top: 1747px; background: linear-gradient(180deg, #5f9ad6 0%, #bcd8f0 40%, #f1f1f1 65%, #7f8a76 100%); }
  .p3 { left: 173px; top: 1996px; background: linear-gradient(180deg, #3d78c4 0%, #8fb5e0 30%, #e57a23 60%, #d85d18 85%, #6f7a3c 100%); }
  .p4 { left: 607px; top: 1996px; background: linear-gradient(180deg, #8fbde6 0%, #d5e7f4 35%, #f2f2f0 60%, #4db5c9 85%, #8a8f86 100%); }
  .projects-more { left: 544px; top: 2260px; width: 112px; height: 35px; line-height: 35px; }

  /* News */
  .news-band { position: absolute; top: 2335px; left: 0; width: 1200px; height: 369px; background: var(--news-bg); }
  .news-title { position: absolute; left: 168px; top: 42px; font-size: 24px; font-weight: 400; color: var(--text-dark); }
  .news-arrows { position: absolute; left: 652px; top: 50px; }
  .news-item { position: absolute; width: 260px; }
  .news-date { position: absolute; left: 0; top: 4px; width: 44px; text-align: center; }
  .news-date .day { display: block; height: 34px; line-height: 34px; background: var(--white); font-size: 24px; font-weight: 700; color: var(--text-dark); }
  .news-date .mon { display: block; height: 16px; line-height: 16px; background: var(--brand-blue); color: var(--white); font-size: 9px; }
  .news-body { margin-left: 56px; }
  .news-body h3 { font-size: 11px; font-weight: 700; line-height: 15px; color: var(--text-dark); }
  .news-body p { font-size: 11px; font-style: italic; line-height: 15px; color: var(--text-muted); margin-top: 2px; }
  .news-body a { display: block; font-size: 11px; font-weight: 600; color: var(--brand-blue); text-decoration: none; margin-top: 2px; }
  .n1 { left: 170px; top: 93px; }
  .n2 { left: 453px; top: 93px; }
  .n3 { left: 170px; top: 226px; }
  .n4 { left: 453px; top: 226px; }

  /* Estimate request form */
  .quick-contact { position: absolute; left: 747px; top: 37px; width: 280px; height: 290px; background: var(--brand-blue); border-radius: 4px; padding: 16px 18px 0 19px; }
  .quick-contact h2 { font-weight: 400; font-size: 24px; line-height: 28px; color: var(--white); margin-bottom: 7px; }
  .field { display: block; width: 247px; height: 27px; background: var(--white); border: 0; font-size: 11px; color: #888; padding: 6px 8px; margin-bottom: 6px; font-family: inherit; }
  .field.message { height: 56px; resize: none; }
  .submit { display: block; width: 89px; height: 26px; background: var(--accent-green); color: var(--deep-navy); font-size: 11px; border: 0; font-family: inherit; margin-top: 6px; }

  /* Footer */
  .site-footer { position: absolute; top: 2704px; left: 0; width: 1200px; height: 98px; background: var(--footer-bg); }
  .footer-social { left: 556px; top: 26px; }
  .footer-social span { background: #9a9a9a; }
  .copyright { position: absolute; top: 60px; width: 1200px; text-align: center; font-size: 12px; color: #d0d0d0; }
  .copyright b { color: var(--white); font-weight: 600; }
</style>
</head>
<body>

<header class="site-header">
  <div class="brand">
    <div class="brand-square"></div>
    <div class="brand-name">Bluefinch<br>Painting</div>
  </div>
  <div class="social header-social"><span></span><span></span><span></span><span></span></div>
  <div class="phone">
    <svg width="20" height="20" viewBox="0 0 24 24"><path fill="#0b63af" d="M6.6 10.8c1.4 2.8 3.8 5.1 6.6 6.6l2.2-2.2c.3-.3.7-.4 1-.2 1.1.4 2.3.6 3.6.6.6 0 1 .4 1 1V20c0 .6-.4 1-1 1C10.6 21 3 13.4 3 4c0-.6.4-1 1-1h3.5c.6 0 1 .4 1 1 0 1.3.2 2.5.6 3.6.1.3 0 .7-.2 1l-2.3 2.2z"/></svg>
    <span>(555) 318-7046</span>
  </div>
</header>

<nav class="main-nav">
  <span class="nav-item active" style="left:159px">HOME</span>
  <span class="nav-item" style="left:262px">ABOUT US</span>
  <span class="nav-item" style="left:371px">SERVICES</span>
  <span class="nav-item" style="left:479px">PROJECTS</span>
  <span class="nav-item" style="left:586px">CONTACT US</span>
  <span class="quote-btn">GET A FREE QUOTE</span>
</nav>

<section class="hero">
  <div class="hero-photo" role="img" aria-label="Painters in blue shirts and white trousers painting a white wall with a brush and roller"></div>
  <div class="hero-caption">CREATE YOUR WORLD WITH US
    <div class="slider-dots"><i></i><i></i><i class="on"></i><i></i><i></i></div>
  </div>
</section>

<section class="quality">
  <h1>QUALITY PAINTING</h1>
  <h2>CONTRACTOR</h2>
  <p>We bring careful preparation, clean lines and lasting finishes to every room we touch. Our crew protects your floors and furniture, explains each step, and keeps the site tidy from the first coat to the final walkthrough. Homeowners trust us for honest estimates, on-time starts and colours that look exactly as planned. Interior or exterior, one room or a whole house, we treat your home like our own.</p>
  <span class="btn-green">READ MORE</span>
  <div class="quality-photo" role="img" aria-label="Living room with bright orange and yellow painted walls"></div>
</section>

<section class="services">
  <div class="services-photo" role="img" aria-label="Open paint cans in many colours with brushes and a roller"></div>
  <h2>OUR SERVICES</h2>
  <p>From fresh siding to a single accent wall, we handle projects of every size with skilled hands and quality paints that last.</p>
  <ul class="service-list">
    <li>EXTERIOR PAINTING</li>
    <li>INTERIOR PAINTING</li>
    <li>RESIDENTIAL PAINTING</li>
    <li>COMMERCIAL PAINTING</li>
  </ul>
  <span class="btn-blue">MORE</span>
</section>

<section class="banner" role="img" aria-label="Paint cans on a floor and a hand rolling yellow paint onto a wall">
  <div class="banner-title"><span class="l1">PROFESSIONAL</span><span class="l2">PAINTING WORKERS</span></div>
</section>

<h2 class="projects-title">OUR PROJECTS</h2>
<div class="project p1" role="img" aria-label="Bedroom with a red feature wall"></div>
<div class="project p2" role="img" aria-label="Modern white two-storey house"></div>
<div class="project p3" role="img" aria-label="Building with orange striped exterior"></div>
<div class="project p4" role="img" aria-label="White modern villa with a pool"></div>
<span class="btn-blue projects-more">MORE</span>

<section class="news-band">
  <h2 class="news-title">LATEST NEWS</h2>
  <svg class="news-arrows" width="32" height="16" viewBox="0 0 32 16"><path d="M8 2 L2 8 L8 14M24 2 L30 8 L24 14" fill="none" stroke="#999" stroke-width="1.5"/></svg>

  <article class="news-item n1">
    <div class="news-date"><span class="day">10</span><span class="mon">JUNE</span></div>
    <div class="news-body"><h3>FRESH COLOURS FOR SPRING</h3><p>Soft blues and warm whites lead this season's most requested interiors.</p><a>- READ MORE</a></div>
  </article>
  <article class="news-item n2">
    <div class="news-date"><span class="day">15</span><span class="mon">JUNE</span></div>
    <div class="news-body"><h3>PROTECTING YOUR SIDING</h3><p>A good coat of exterior paint guards wood against rain and sun.</p><a>- READ MORE</a></div>
  </article>
  <article class="news-item n3">
    <div class="news-date"><span class="day">22</span><span class="mon">JUNE</span></div>
    <div class="news-body"><h3>CHOOSING THE RIGHT FINISH</h3><p>Matte, eggshell or gloss: how sheen changes the feel of a room.</p><a>- READ MORE</a></div>
  </article>
  <article class="news-item n4">
    <div class="news-date"><span class="day">30</span><span class="mon">JUNE</span></div>
    <div class="news-body"><h3>NEW CREW MEMBERS JOIN US</h3><p>Our team grows to serve more homeowners across the region this year.</p><a>- READ MORE</a></div>
  </article>

  <form class="quick-contact">
    <h2>QUICK CONTACT</h2>
    <input class="field" type="text" placeholder="Name">
    <input class="field" type="text" placeholder="Mobile">
    <input class="field" type="text" placeholder="Address">
    <input class="field" type="text" placeholder="E-mail">
    <textarea class="field message" placeholder="Painting project description"></textarea>
    <button class="submit" type="button">SUBMIT</button>
  </form>
</section>

<footer class="site-footer">
  <div class="social footer-social abs"><span></span><span></span><span></span><span></span></div>
  <p class="copyright">© 2015. <b>Bluefinch Painting.</b> bluefinchpainting.example · All rights reserved.</p>
</footer>

</body>
</html>
```